Stationery and Business Card Design

We need stationary design for our new company lanternfold. Lanternfold is a company that provides city apartment rentals for tourists in Athens We need business cards, letterheads for A4 and A5 and envelopes for A4 A5. The design needs to be modern, friendly and corporate.

Target Market(s)

City Tourists

Industry/Entity Type

Tourism

```html
<!DOCTYPE html>
<html lang="en">
<head>
<meta charset="UTF-8">
<title>Lanternfold Business Cards</title>
<link href="https://fonts.googleapis.com/css2?family=Quicksand:wght@400;500;600&display=swap" rel="stylesheet">
<style>
  :root {
    --backdrop: #eef2f2;
    --plum: #931f8e;
    --plum-light: #a2399c;
    --paper: #ffffff;
    --ink-light: #ffffff;
  }
  html, body {
    margin: 0;
    padding: 0;
    width: 1200px;
    height: 1000px;
    overflow: hidden;
    background: var(--backdrop);
    font-family: "Quicksand", sans-serif;
  }
  .canvas {
    position: relative;
    width: 1200px;
    height: 1000px;
  }
  .card {
    position: absolute;
    width: 620px;
    height: 340px;
    overflow: hidden;
    box-shadow: 0 3px 8px rgba(0,0,0,0.18);
  }
  .card--back {
    left: 340px;
    top: 110px;
    background: var(--paper);
  }
  .card--front {
    left: 240px;
    top: 540px;
    background: var(--plum);
  }
  .card__shapes {
    position: absolute;
    inset: 0;
  }
  .brand {
    position: absolute;
    display: flex;
    align-items: center;
    color: var(--plum);
    font-weight: 500;
  }
  .brand__mark {
    background: var(--plum);
  }
  .card--back .brand {
    left: 34px;
    top: 150px;
    gap: 10px;
    font-size: 27px;
  }
  .card--back .brand__mark {
    width: 26px;
    height: 26px;
  }
  .identity {
    position: absolute;
    right: 36px;
    top: 44px;
    text-align: right;
    color: var(--ink-light);
    font-weight: 400;
  }
  .identity__name {
    font-size: 24px;
    letter-spacing: 0.5px;
    margin: 0;
  }
  .identity__role {
    font-size: 18px;
    margin: 2px 0 0;
  }
  .contacts {
    position: absolute;
    right: 36px;
    top: 150px;
    margin: 0;
    padding: 0;
    list-style: none;
    color: var(--ink-light);
    font-size: 14px;
  }
  .contacts__item {
    display: flex;
    justify-content: flex-end;
    align-items: center;
    gap: 10px;
    height: 31px;
  }
  .contacts__icon {
    width: 20px;
    height: 20px;
    flex: none;
  }
  .card__inner {
    position: absolute;
    inset: 18px;
    background: var(--paper);
  }
  .card--front .brand {
    left: 0;
    right: 0;
    top: 0;
    bottom: 0;
    flex-direction: column;
    justify-content: center;
    gap: 18px;
    font-size: 58px;
  }
  .card--front .brand__mark {
    width: 96px;
    height: 96px;
  }
</style>
</head>
<body>
<main class="canvas">

  <section class="card card--back" aria-label="Business card, contact side">
    <svg class="card__shapes" width="620" height="340" viewBox="0 0 620 340">
      <defs>
        <linearGradient id="plumField" x1="0" y1="0" x2="1" y2="1">
          <stop offset="0" stop-color="#a2399c"/>
          <stop offset="0.6" stop-color="#931f8e"/>
          <stop offset="1" stop-color="#8f1c8a"/>
        </linearGradient>
      </defs>
      <polygon points="172,0 620,0 620,340 262,340 318,150" fill="url(#plumField)"/>
      <polygon points="146,0 162,0 306,150 246,340 230,340 288,150" fill="var(--plum)"/>
    </svg>

    <div class="brand">
      <span class="brand__mark"></span>
      <span class="brand__name">Lanternfold</span>
    </div>

    <div class="identity">
      <p class="identity__name">YOUR NAME</p>
      <p class="identity__role">Your Postion</p>
    </div>

    <ul class="contacts">
      <li class="contacts__item">000-0000-000
        <svg class="contacts__icon" viewBox="0 0 20 20"><circle cx="10" cy="10" r="9" fill="none" stroke="#fff" stroke-width="1.2"/><rect x="7" y="4.5" width="6" height="11" rx="1" fill="none" stroke="#fff" stroke-width="1.2"/><line x1="9" y1="13.5" x2="11" y2="13.5" stroke="#fff" stroke-width="1.2"/></svg>
      </li>
      <li class="contacts__item">lanternfold@mailbox.com
        <svg class="contacts__icon" viewBox="0 0 20 20"><circle cx="10" cy="10" r="9" fill="none" stroke="#fff" stroke-width="1.2"/><rect x="5" y="6.5" width="10" height="7" fill="none" stroke="#fff" stroke-width="1.2"/><polyline points="5,6.5 10,10.5 15,6.5" fill="none" stroke="#fff" stroke-width="1.2"/></svg>
      </li>
      <li class="contacts__item">www.lanternfold.com
        <svg class="contacts__icon" viewBox="0 0 20 20"><circle cx="10" cy="10" r="9" fill="none" stroke="#fff" stroke-width="1.2"/><circle cx="10" cy="10" r="5.5" fill="none" stroke="#fff" stroke-width="1"/><ellipse cx="10" cy="10" rx="2.3" ry="5.5" fill="none" stroke="#fff" stroke-width="1"/><line x1="4.5" y1="10" x2="15.5" y2="10" stroke="#fff" stroke-width="1"/></svg>
      </li>
      <li class="contacts__item">www.lanternfold.com
        <svg class="contacts__icon" viewBox="0 0 20 20"><circle cx="10" cy="10" r="9" fill="#fff"/><polygon points="10,4.5 15,9.5 13.5,9.5 13.5,14.5 6.5,14.5 6.5,9.5 5,9.5" fill="var(--plum)"/></svg>
      </li>
      <li class="contacts__item">Your Address</li>
    </ul>
  </section>

  <section class="card card--front" aria-label="Business card, brand side">
    <div class="card__inner">
      <div class="brand">
        <span class="brand__mark"></span>
        <span class="brand__name">Lanternfold</span>
      </div>
    </div>
  </section>

</main>
</body>
</html>
```